A website for a Maltese Law Firm

Our law firm needs a website to further its business. The site should have a simple yet effective design. We would need the following sections: About us, Practice Areas, About Malta, Contact. These should be further split as follows:

About us: Our firm, Our values, What others say, Offices

Practice Areas: Crimimal, Citizenship & Residence, Sovereign Patron Pathway, Criminal Defence, Civil Litigation, Arbitration and ADR, Commercial and Corporate, Media Law.

About Malta: just one section.

Contact: Just one section

We would also need a news feed at the front of the site to include latest news regarding our cases.

At the bottom we need a section for our Terms and a Privacy Statement.

Our logo is being attached.

Target Market(s)

All clients looking for legal assistance in Malta

Industry/Entity Type

Legal

Coding

Coded - Design and coding required

Number of Pages Required

1 page

Requirements
Must have
• It must be simple yet striking.

```html
<!DOCTYPE html>
<html lang="en">
<head>
<meta charset="utf-8">
<title>Marlow &amp; Ferrante Advocates</title>
<link href="https://fonts.googleapis.com/css2?family=Raleway:wght@400;500;600;700&family=Roboto:wght@400;500;700&display=swap" rel="stylesheet">
<style>
:root{
  --ink:#111111;
  --text:#333333;
  --muted:#555555;
  --white:#ffffff;
  --line:#dddddd;
  --band:#6e6d6d;
  --news-bg:#f2f2f2;
  --footer:#000000;
  --footer-text:#8a8a8a;
  --hero-dark:#2a2522;
  --hero-mid:#6b6561;
}
*{margin:0;padding:0;box-sizing:border-box}
html,body{width:1200px;height:2426px;overflow:hidden}
body{font-family:"Roboto",Arial,sans-serif;color:var(--text);background:var(--white);position:relative}
.abs{position:absolute}

/* header */
.site-header{position:absolute;left:0;top:0;width:1200px;height:103px;background:var(--white)}
.brand{position:absolute;left:133px;top:28px;width:326px;text-align:center;font-family:"Raleway",sans-serif;font-weight:500;color:var(--ink)}
.brand .rule{height:2px;background:var(--ink)}
.brand .name{font-size:33px;letter-spacing:1px;line-height:40px;text-transform:uppercase}
.brand .sub{font-size:11px;letter-spacing:6px;line-height:12px;margin-bottom:3px;text-transform:uppercase}
.call{position:absolute;right:132px;top:18px;display:flex;align-items:center;gap:10px;font-family:"Raleway",sans-serif}
.call .lbl{font-size:11px;letter-spacing:1.5px;font-weight:600;text-transform:uppercase}
.call .num{font-size:18px;font-weight:600;color:var(--ink)}
.nav{position:absolute;right:131px;top:60px;display:flex;gap:6px}
.nav a{font-family:"Raleway",sans-serif;font-size:13.5px;font-weight:500;color:var(--ink);text-decoration:none;padding:5px 12px}
.nav a.active{background:var(--ink);color:var(--white);font-weight:700}

/* hero */
.hero{position:absolute;left:0;top:103px;width:1200px;height:491px;background:linear-gradient(100deg,var(--hero-mid) 0%,#8a8581 45%,#5c5651 75%,var(--hero-dark) 100%)}
.hero-photo{position:absolute;left:0;top:0;width:670px;height:491px;background:radial-gradient(ellipse at 45% 40%,#b59a86 0%,#5c4c44 40%,rgba(40,34,32,0) 75%)}
.hero-copy{position:absolute;left:674px;top:128px;width:290px;color:var(--white);font-family:"Raleway",sans-serif;text-align:center}
.hero-copy .rule{height:2px;background:var(--white)}
.hero-copy .name{font-size:25px;font-weight:500;letter-spacing:1px;line-height:30px;text-transform:uppercase}
.hero-copy .sub{font-size:9px;letter-spacing:5px;margin-bottom:2px}
.hero-copy h1{font-size:58px;font-weight:700;line-height:60px;margin-top:16px;text-align:left;letter-spacing:1px}
.btn-hero{position:absolute;left:679px;top:365px;width:285px;height:57px;background:var(--ink);color:var(--white);font-family:"Raleway",sans-serif;font-size:16px;font-weight:600;letter-spacing:2.5px;display:flex;align-items:center;justify-content:center;gap:10px}
.dots{position:absolute;left:530px;top:432px;display:flex;gap:18px;align-items:center}
.dots span{width:12px;height:12px;border-radius:50%;background:var(--white)}
.dots span.on{width:16px;height:16px;background:transparent;border:2px solid var(--white)}

/* section title */
.sec-title{position:absolute;left:0;width:1200px;text-align:center}
.sec-title span{display:inline-block;font-family:"Raleway",sans-serif;font-size:22px;font-weight:500;color:var(--ink);padding:10px 12px;border-top:2px solid var(--ink);border-bottom:2px solid var(--ink);letter-spacing:.5px}

/* practice */
.practice{position:absolute;left:0;top:594px;width:1200px;height:646px;background:var(--white)}
.area{position:absolute;width:236px;text-align:center}
.area .icon{width:74px;height:74px;margin:0 auto;border:2px solid var(--ink);border-radius:50%;display:flex;align-items:center;justify-content:center}
.area h3{font-family:"Raleway",sans-serif;font-weight:700;font-size:12px;color:var(--ink);height:40px;display:flex;align-items:center;justify-content:center;margin-top:12px;line-height:16px;text-transform:uppercase}
.area p{font-size:12px;line-height:17.5px;color:var(--muted);width:195px;margin:4px auto 0}
.vline{position:absolute;width:1px;height:205px;background:var(--line)}
.hline{position:absolute;height:1px;width:205px;background:#ebebeb}

/* welcome */
.welcome{position:absolute;left:0;top:1240px;width:1200px;height:437px;background:var(--band);color:var(--white)}
.welcome .kicker{position:absolute;left:133px;top:44px;width:290px;font-family:"Raleway",sans-serif}
.welcome .kicker .top{font-size:12px;font-weight:600;letter-spacing:1px;border-top:2px solid var(--white);padding-top:8px}
.welcome .kicker .name{font-size:25px;font-weight:500;letter-spacing:1px;text-transform:uppercase;border-bottom:2px solid var(--white);padding-bottom:6px;line-height:32px}
.welcome .lead{position:absolute;left:133px;top:140px;width:440px;font-size:12px;font-weight:700;line-height:19px}
.welcome .body{position:absolute;left:133px;top:192px;width:474px;font-size:12px;line-height:18px;text-align:justify}
.btn-dark{background:var(--ink);color:var(--white);font-family:"Raleway",sans-serif;font-weight:700;display:flex;align-items:center;justify-content:center;gap:8px}
.welcome .btn-dark{position:absolute;left:133px;top:332px;width:126px;height:38px;font-size:12px}
.welcome .photo{position:absolute;left:642px;top:47px;width:427px;height:346px;background:linear-gradient(135deg,#d9d2c8 0%,#8b7a6a 35%,#3b302b 60%,#6a4a34 100%)}

/* news */
.news{position:absolute;left:0;top:1677px;width:1200px;height:506px;background:var(--news-bg)}
.card{position:absolute;top:128px;width:300px;height:325px;background:var(--white);border:2px solid #dcdcdc}
.card .img{position:absolute;left:5px;top:5px;width:287px;height:140px}
.card .date{position:absolute;right:4px;top:4px;width:38px;height:54px;background:var(--ink);color:var(--white);text-align:center;font-family:"Raleway",sans-serif;font-weight:700;line-height:12px;padding-top:6px}
.card .date b{display:block;font-size:15px;line-height:18px}
.card .date i{display:block;font-style:normal;font-size:8px}
.card h4{position:absolute;left:25px;top:163px;width:250px;font-family:"Raleway",sans-serif;font-size:12px;font-weight:700;color:var(--ink);line-height:18px;text-transform:uppercase}
.card p{position:absolute;left:25px;top:204px;width:250px;font-size:11.5px;line-height:17px;color:var(--muted);text-align:justify}
.card .btn-dark{position:absolute;left:25px;top:280px;width:70px;height:22px;font-size:10px}
.arrow{position:absolute;top:1951px;width:36px;height:38px;background:var(--ink);display:flex;align-items:center;justify-content:center}

/* footer */
.site-footer{position:absolute;left:0;top:2183px;width:1200px;height:243px;background:var(--footer);color:var(--white)}
.site-footer .brand{left:133px;top:46px;width:290px;color:var(--white)}
.site-footer .brand .rule{background:var(--white)}
.site-footer .brand .name{font-size:29px;line-height:34px}
.follow{position:absolute;left:161px;top:131px;display:flex;align-items:center;gap:8px;font-family:"Raleway",sans-serif;font-weight:700;font-size:11px;letter-spacing:.5px}
.follow .lbl{margin-right:12px}
.follow i{width:22px;height:22px;border-radius:50%;display:block;background:#4a4a4a}
.terms{position:absolute;left:472px;top:43px;width:598px}
.terms h5{font-family:"Raleway",sans-serif;font-size:11.5px;font-weight:700;letter-spacing:.3px}
.terms p{margin-top:18px;font-size:11px;line-height:18px;color:var(--footer-text);text-align:justify}
.legal-line{position:absolute;left:133px;top:176px;width:936px;height:1px;background:#2a2a2a}
.legal{position:absolute;left:0;top:196px;width:1200px;text-align:center;font-size:10px;color:var(--footer-text)}
</style>
</head>
<body>

<header class="site-header">
  <div class="brand">
    <div class="rule"></div>
    <div class="name">Marlow &amp; Ferrante</div>
    <div class="sub">Advocates</div>
    <div class="rule"></div>
  </div>
  <div class="call">
    <svg width="22" height="22" viewBox="0 0 22 22"><circle cx="11" cy="11" r="11" fill="#111"/><path d="M7.5 6.2c.5-.4 1.2-.3 1.5.2l.9 1.6c.3.5.1 1-.3 1.3l-.6.4c.5 1.1 1.4 2 2.5 2.5l.4-.6c.3-.4.9-.6 1.3-.3l1.6.9c.5.3.6 1 .2 1.5l-.6.7c-.5.5-1.2.7-1.9.5-2.6-.8-4.6-2.8-5.4-5.4-.2-.7 0-1.4.5-1.9z" fill="#fff"/></svg>
    <span class="lbl">Call us now</span>
    <span class="num">(356) 2100 4455</span>
  </div>
  <nav class="nav">
    <a class="active" href="#">Home</a>
    <a href="#">About us</a>
    <a href="#">Practice Areas</a>
    <a href="#">About Malta</a>
    <a href="#">Contact us</a>
  </nav>
</header>

<section class="hero">
  <div class="hero-photo" role="img" aria-label="Photograph of a smiling advocate in a black court gown against a grey studio backdrop"></div>
  <div class="hero-copy">
    <div class="rule"></div>
    <div class="name">Marlow &amp; Ferrante</div>
    <div class="sub">ADVOCATES</div>
    <div class="rule"></div>
    <h1>LAW FIRM</h1>
  </div>
  <div class="btn-hero" style="top:262px">LEARN MORE <svg width="9" height="12" viewBox="0 0 9 12"><path d="M0 0L9 6L0 12Z" fill="#fff"/></svg></div>
  <div class="dots"><span></span><span class="on"></span><span></span><span></span><span></span></div>
</section>

<section class="practice">
  <div class="sec-title" style="top:38px"><span>OUR PRACTICE AREAS</span></div>

  <div class="vline" style="left:356px;top:130px"></div>
  <div class="vline" style="left:603px;top:130px"></div>
  <div class="vline" style="left:850px;top:130px"></div>
  <div class="vline" style="left:356px;top:388px"></div>
  <div class="vline" style="left:603px;top:388px"></div>
  <div class="vline" style="left:850px;top:388px"></div>
  <div class="hline" style="left:133px;top:363px"></div>
  <div class="hline" style="left:375px;top:363px"></div>
  <div class="hline" style="left:620px;top:363px"></div>
  <div class="hline" style="left:865px;top:363px"></div>

  <!-- row 1 -->
  <div class="area" style="left:121px;top:140px">
    <div class="icon"><svg width="40" height="40" viewBox="0 0 40 40" fill="none" stroke="#111" stroke-width="2"><circle cx="12" cy="26" r="7"/><circle cx="28" cy="26" r="7"/><path d="M12 19V10M28 19V10M12 10h16"/></svg></div>
    <h3>Crimnal</h3>
    <p>There are many variations of passages of Lorem Ipsum available, but the majority.</p>
  </div>
  <div class="area" style="left:356px;top:140px">
    <div class="icon"><svg width="40" height="40" viewBox="0 0 40 40" fill="none" stroke="#111" stroke-width="2"><rect x="8" y="6" width="20" height="28" rx="1"/><circle cx="22" cy="22" r="7" fill="#fff"/><path d="M15 22h14M22 15v14"/></svg></div>
    <h3>Citizenship &amp;<br>Residence</h3>
    <p>It is a long established fact that a reader will be distracted by the readable content .</p>
  </div>
  <div class="area" style="left:603px;top:140px">
    <div class="icon"><svg width="40" height="40" viewBox="0 0 40 40" fill="#111"><circle cx="15" cy="13" r="6"/><path d="M5 34c0-8 4-12 10-12s10 4 10 12z"/><text x="25" y="17" font-size="13" font-family="Roboto,sans-serif" font-weight="700">$</text><rect x="27" y="26" width="3" height="8"/><rect x="32" y="22" width="3" height="12"/></svg></div>
    <h3>Sovereign Patron<br>Pathway</h3>
    <p>Sed ut perspiciatis unde omnis iste natus error sit voluptatem accusantium.</p>
  </div>
  <div class="area" style="left:850px;top:140px">
    <div class="icon"><svg width="40" height="40" viewBox="0 0 40 40" fill="none" stroke="#111" stroke-width="2.2"><path d="M20 5l12 4v10c0 8-6 13-12 16C14 32 8 27 8 19V9z"/><circle cx="20" cy="19" r="4"/></svg></div>
    <h3>Criminal Defence</h3>
    <p>But I must explain to you how all this mistaken idea of denouncing pleasure</p>
  </div>

  <!-- row 2 -->
  <div class="area" style="left:121px;top:398px">
    <div class="icon"><svg width="40" height="40" viewBox="0 0 40 40" fill="none" stroke="#111" stroke-width="2"><rect x="12" y="6" width="16" height="28"/><path d="M16 11h2M22 11h2M16 16h2M22 16h2M16 21h2M22 21h2M16 26h2M22 26h2"/></svg></div>
    <h3>Civil Litigation</h3>
    <p>There are many variations of passages of Lorem Ipsum available, but the majority.</p>
  </div>
  <div class="area" style="left:356px;top:398px">
    <div class="icon"><svg width="40" height="40" viewBox="0 0 40 40" fill="#111"><circle cx="18" cy="10" r="4"/><path d="M12 16h12v10H12z"/><path d="M26 14l7-5 2 2-7 5z"/><rect x="8" y="30" width="24" height="3"/><rect x="12" y="27" width="16" height="3"/></svg></div>
    <h3>Arbitration<br>and ADR</h3>
    <p>It is a long established fact that a reader will be distracted by the readable content .</p>
  </div>
  <div class="area" style="left:603px;top:398px">
    <div class="icon"><svg width="40" height="40" viewBox="0 0 40 40" fill="#111"><path d="M20 5L34 12H6z"/><rect x="9" y="14" width="3" height="14"/><rect x="16" y="14" width="3" height="14"/><rect x="22" y="14" width="3" height="14"/><rect x="28" y="14" width="3" height="14"/><rect x="6" y="30" width="28" height="3"/></svg></div>
    <h3>Commercial and<br>Corporate</h3>
    <p>Sed ut perspiciatis unde omnis iste natus error sit voluptatem accusantium.</p>
  </div>
  <div class="area" style="left:850px;top:398px">
    <div class="icon"><svg width="40" height="40" viewBox="0 0 40 40" fill="none" stroke="#111" stroke-width="2.2"><rect x="7" y="12" width="26" height="19" rx="2"/><path d="M15 5l5 7 5-7"/><rect x="11" y="16" width="15" height="11" fill="#111"/></svg></div>
    <h3>Media Law</h3>
    <p>But I must explain to you how all this mistaken idea of denouncing pleasure</p>
  </div>
</section>

<section class="welcome">
  <div class="kicker">
    <div class="top">WELCOME TO</div>
    <div class="name">Marlow &amp; Ferrante</div>
  </div>
  <p class="lead">But I must explain to you how all this mistaken idea of denouncing pleasure and praising pain was born and I will give you a complete account of the system</p>
  <p class="body">At vero eos et accusamus et iusto odio dignissimos ducimus qui blanditiis praesentium voluptatum deleniti atque corrupti quos dolores et quas molestias excepturi sint occaecati cupiditate non provident, similique sunt in culpa qui officia deserunt mollitia animi, id est laborum et dolorum fuga. Et harum quidem rerum facilis est et expedita distinctio. Nam libero tempore, cum soluta nobis est eligendi optio cumque nihil impedit quo minus id quod maxime placeat facere possimus,</p>
  <div class="btn-dark">READ MORE <svg width="7" height="10" viewBox="0 0 7 10"><path d="M0 0L7 5L0 10Z" fill="#fff"/></svg></div>
  <div class="photo" role="img" aria-label="Photograph of an advocate in a gown seated at a desk beside a stack of law books in a library office"></div>
</section>

<section class="news">
  <div class="sec-title" style="top:40px"><span>LATEST NEWS</span></div>

  <article class="card" style="left:129px">
    <div class="img" role="img" aria-label="Photograph of a lawyer reading at a desk with a scales of justice figurine and bookshelves" style="background:linear-gradient(120deg,#6b4a2e,#c9b9a6 55%,#3f3a3a)"></div>
    <div class="date"><b>28</b><i>MAY</i><i>2016</i></div>
    <h4>But I must explain to you how all this mistaken idea</h4>
    <p>At vero eos et accusamus et iusto odio dignissimos ducimus qui blanditiis praesentium voluptatum deleniti .</p>
    <div class="btn-dark">READ MORE</div>
  </article>
  <article class="card" style="left:450px">
    <div class="img" role="img" aria-label="Photograph of a barrister's wig resting on old leather-bound books" style="background:linear-gradient(120deg,#2a1a10,#8a6a44 50%,#2e1e14)"></div>
    <div class="date"><b>28</b><i>MAY</i><i>2016</i></div>
    <h4>It is a long established fact that a reader will be distracted</h4>
    <p>At vero eos et accusamus et iusto odio dignissimos ducimus qui blanditiis praesentium voluptatum deleniti .</p>
    <div class="btn-dark">READ MORE</div>
  </article>
  <article class="card" style="left:770px">
    <div class="img" role="img" aria-label="Photograph of a hand writing with a pen beside an open law book and red volumes" style="background:linear-gradient(120deg,#7a2a22,#d8cfc4 55%,#f1ece6)"></div>
    <div class="date"><b>28</b><i>MAY</i><i>2016</i></div>
    <h4>There are many variations of passages of Lorem Ipsum.</h4>
    <p>At vero eos et accusamus et iusto odio dignissimos ducimus qui blanditiis praesentium voluptatum deleniti .</p>
    <div class="btn-dark">READ MORE</div>
  </article>
</section>
<div class="arrow" style="left:68px"><svg width="9" height="14" viewBox="0 0 9 14"><path d="M8 1L2 7l6 6" fill="none" stroke="#fff" stroke-width="2.4"/></svg></div>
<div class="arrow" style="left:1088px"><svg width="9" height="14" viewBox="0 0 9 14"><path d="M1 1l6 6-6 6" fill="none" stroke="#fff" stroke-width="2.4"/></svg></div>

<footer class="site-footer">
  <div class="brand">
    <div class="rule"></div>
    <div class="name">Marlow &amp; Ferrante</div>
    <div class="sub">Advocates</div>
    <div class="rule"></div>
  </div>
  <div class="follow"><span class="lbl">FOLLOW US ON</span><i></i><i></i><i></i><i></i></div>
  <div class="terms">
    <h5>TERMS AND PRIVACY</h5>
    <p>Sed ut perspiciatis unde omnis iste natus error sit voluptatem accusantium doloremque laudantium, totam rem aperiam, eaque ipsa quae ab illo inventore veritatis et quasi architecto beatae vitae dicta sunt explicabo. Nemo enim ipsam voluptatem quia voluptas sit aspernatur aut odit aut fugit, sed quia consequuntur.</p>
  </div>
  <div class="legal-line"></div>
  <div class="legal">Terms &amp; Conditions &nbsp;|&nbsp; Privacy Statement &nbsp;|&nbsp; Copyrights @ 2016 All Rights Reserveed</div>
</footer>

</body>
</html>
```